Business card for Crestline Bathrooms

Please design a business card for our bathroom renovation business. You can use my existing logo, but if you have an idea to modernize it, I would like to see it. Please see attached files first. I would like to use the blue and the orange theme. I like the concept of using the shower head in the logo. Please find following a design (or two) that I have been trying to create with my limited resources. That design was for a sign, but I was going to adopt it and use it as a business card as well. I like the concept of the water splash but I don’t think it “flows” nicely together with the logo. Another thought is that maybe creating the logo out of water splash could work and have a dramatic effect (like the water text and the butterfly picture attached with similar background instead of white). If the above doesn’t work I would like to see a modern simplified design. One of the attached files named as the unwanted business card has all the details that I want included in the business card. Please note that it is two sided.
Updates

I am very thankful for the designs that I have received, but they are very similar and only a couple of attempts to do something with the water splash as per my original brief. Modernizing the logo and having it made out of out of water splash with the orange as color accent could work and have a dramatic effect (like the water text and the butterfly picture attached with similar background instead of white). Please do not use the butterfly itself! This is just an example that images can be created out of water splash.

Contact Information for Business Card

all the details are on the unwonted business card file included

Colors
3176b5

Requirements
Nice to have
• Copied from the brief:
• ... maybe creating the logo out of water splash could work and have a dramatic effect (like the water text and the butterfly picture attached with similar background instead of white). Please do not use the butterfly itself!
Should not have
• I am getting designs with a butterfly. The butterfly picture was an example of creating something from a water splash. The butterfly itself has no association with anything other than the concept of creating a logo out of water splash. Sorry, I thought I was clear in the brief.

```html
<!DOCTYPE html>
<html lang="en">
<head>
<meta charset="utf-8">
<title>Crestline Bathrooms – Business Card</title>
<link rel="stylesheet" href="https://fonts.googleapis.com/css2?family=Roboto:wght@400;500&family=Short+Stack&display=swap">
<style>
  :root {
    --page: #e4e4e4;
    --navy: #1b3254;
    --navy-deep: #152a48;
    --splash-blue: #3a5f8c;
    --splash-light: #c9d6e3;
    --coral: #ec7463;
    --white: #ffffff;
  }
  html, body {
    margin: 0;
    width: 1200px;
    height: 960px;
    overflow: hidden;
    background: var(--page);
    font-family: "Roboto", Arial, sans-serif;
  }
  .canvas { position: relative; width: 1200px; height: 960px; }
  .card {
    position: absolute;
    width: 600px;
    height: 342px;
    background: var(--navy);
    overflow: hidden;
    color: var(--white);
  }
  .card--front { left: 302px; top: 125px; }
  .card--back { left: 299px; top: 493px; }

  .splash { position: absolute; top: 0; bottom: 0; width: 300px; }
  .card--front .splash {
    left: 0;
    background:
      radial-gradient(ellipse 70% 35% at 40% 92%, rgba(201,214,227,0.75), transparent 70%),
      radial-gradient(ellipse 30% 50% at 8% 70%, rgba(201,214,227,0.45), transparent 70%),
      linear-gradient(90deg, var(--splash-blue), var(--navy) 90%);
  }
  .card--back .splash {
    right: 0;
    background:
      radial-gradient(ellipse 70% 35% at 60% 92%, rgba(201,214,227,0.75), transparent 70%),
      radial-gradient(ellipse 30% 50% at 92% 70%, rgba(201,214,227,0.45), transparent 70%),
      linear-gradient(270deg, var(--splash-blue), var(--navy) 90%);
  }

  .holder-name {
    position: absolute;
    right: 52px;
    top: 86px;
    margin: 0;
    font-family: "Short Stack", "Comic Sans MS", cursive;
    font-weight: 400;
    font-size: 23px;
    color: var(--coral);
    letter-spacing: 0.5px;
  }
  .contact-list {
    position: absolute;
    right: 52px;
    top: 130px;
    margin: 0;
    padding: 0;
    list-style: none;
    font-size: 14px;
    line-height: 19px;
    text-align: right;
  }
  .contact-list li { display: flex; justify-content: flex-end; align-items: center; gap: 8px; }
  .contact-list svg { width: 12px; height: 12px; fill: var(--coral); }
  .address {
    position: absolute;
    right: 52px;
    top: 220px;
    margin: 0;
    font-size: 14px;
  }

  .brand {
    position: absolute;
    left: 36px;
    top: 96px;
    display: flex;
    align-items: center;
    gap: 10px;
    font-size: 26px;
    font-weight: 500;
    color: var(--white);
  }
  .brand-dot { width: 14px; height: 14px; border-radius: 50%; background: var(--coral); }

  .services {
    position: absolute;
    left: 34px;
    top: 180px;
    margin: 0;
    padding: 0;
    list-style: none;
    font-size: 13.5px;
    line-height: 17px;
  }
  .services li { display: flex; align-items: center; gap: 8px; }
  .services li::before {
    content: "";
    width: 5px; height: 5px;
    border-radius: 50%;
    background: var(--coral);
  }
  .memberships {
    position: absolute;
    left: 36px;
    top: 268px;
    display: flex;
    align-items: center;
    gap: 16px;
  }
  .badge { background: var(--white); }
  .badge--round { width: 28px; height: 30px; border-radius: 8px; }
  .badge--wide { width: 108px; height: 24px; border-radius: 2px; opacity: 0.9; }
  .divider { width: 1px; height: 32px; background: var(--white); }
</style>
</head>
<body>
<main class="canvas">
  <section class="card card--front" aria-label="Card front">
    <div class="splash" role="img" aria-label="Photograph of water droplets and splash"></div>
    <h1 class="holder-name">Daniel Harcourt</h1>
    <ul class="contact-list">
      <li>6255 0147
        <svg viewBox="0 0 12 12"><path d="M3 0h6a1 1 0 0 1 1 1v10a1 1 0 0 1-1 1H3a1 1 0 0 1-1-1V1a1 1 0 0 1 1-1zm0 1.5v8h6v-8z"/></svg></li>
      <li>0412 555 019
        <svg viewBox="0 0 12 12"><path d="M2.5 0.5l2 2.5-1.2 1.3a7 7 0 0 0 4.4 4.4L9 7.5l2.5 2-1.2 2A9.5 9.5 0 0 1 0.5 1.7z"/></svg></li>
      <li>daniel@crestlinebathrooms.com.au
        <svg viewBox="0 0 12 12"><path d="M0 2h12v8H0zM1 3v.4l5 3.2 5-3.2V3z"/></svg></li>
      <li>www.crestlinebathrooms.com.au
        <svg viewBox="0 0 12 12"><circle cx="6" cy="6" r="5.5"/></svg></li>
    </ul>
    <p class="address">PO Box 48, Kellmont 2619</p>
  </section>

  <section class="card card--back" aria-label="Card back">
    <div class="splash" role="img" aria-label="Photograph of water droplets and splash"></div>
    <div class="brand"><span class="brand-dot"></span>Crestline Bathrooms</div>
    <ul class="services">
      <li>Complete Bathroom Renovations &amp; Remodelling</li>
      <li>Highly Skilled &amp; Qualified Tradespeople</li>
      <li>Professional Service From Concept To Completion</li>
      <li>All Work Guaranteed</li>
    </ul>
    <div class="memberships">
      <span class="badge badge--round"></span>
      <span class="divider"></span>
      <span class="badge badge--wide"></span>
    </div>
  </section>
</main>
</body>
</html>
```